Boutique PEO needs a catchy snail mail and email marketing flyer

Our company provides services to our clients and co-employees throughout the entire life cycle of an employee's employment. It is very serious business to our clients' but we need a catchy message and look to attract the attention of prospective clients. I have attached some of the ideas we tried.

Target Market(s)

small to medium size companies

Font styles to use
Serif

Colors

Designer to choose colors to be used in the design.

```html
<!DOCTYPE html>
<html lang="en">
<head>
<meta charset="utf-8">
<title>PEO Flyers</title>
<link href="https://fonts.googleapis.com/css2?family=Bebas+Neue&display=swap" rel="stylesheet">
<style>
  :root {
    --page-bg: #efebe6;
    --ink: #2e2b29;
    --panel: #eceef1;
    --green: #2f6a34;
    --grey-band: #a9abad;
    --photo-dark: #030303;
    --fur-light: #d9d9dc;
    --fur-shadow: #4a4a4e;
    --studio-dark: #3a3937;
    --studio-mid: #5f5c58;
    --chimp-dark: #2a1e17;
    --chimp-warm: #6b4a35;
  }
  * { margin: 0; padding: 0; box-sizing: border-box; }
  html, body {
    width: 1200px; height: 874px; overflow: hidden;
    background: var(--page-bg);
  }
  .canvas { position: relative; width: 1200px; height: 874px; }
  .flyer {
    position: absolute; top: 72px;
    width: 518px; height: 730px;
    background: var(--panel);
    overflow: hidden;
  }
  .flyer--hanging { left: 70px; }
  .flyer--monkey { left: 614px; }
  .flyer__photo {
    position: absolute; left: 0; top: 0; width: 100%; height: 560px;
  }
  .flyer--hanging .flyer__photo {
    background:
      radial-gradient(ellipse 16% 24% at 48% 38%, rgba(217,217,220,0.55) 0%, rgba(217,217,220,0.18) 55%, rgba(217,217,220,0) 100%),
      radial-gradient(ellipse 26% 40% at 50% 45%, rgba(74,74,78,0.45) 0%, rgba(74,74,78,0) 100%),
      linear-gradient(168deg, rgba(235,232,224,0) 18%, rgba(235,232,224,0.12) 22%, rgba(235,232,224,0) 26%),
      var(--photo-dark);
  }
  .flyer--monkey .flyer__photo {
    background:
      radial-gradient(ellipse 22% 18% at 78% 36%, rgba(140,100,70,0.55) 0%, rgba(140,100,70,0) 100%),
      radial-gradient(ellipse 48% 60% at 56% 62%, var(--chimp-warm) 0%, var(--chimp-dark) 55%, rgba(42,30,23,0) 100%),
      linear-gradient(160deg, var(--studio-mid) 0%, var(--studio-dark) 100%);
  }
  .flyer__curve {
    position: absolute; left: 0; top: 0; width: 518px; height: 730px;
  }
  .flyer__copy {
    position: absolute; left: 0; right: 0; top: 501px;
    text-align: center;
    font-family: "Bebas Neue", "Oswald", sans-serif;
    color: var(--ink);
  }
  .flyer__headline {
    font-size: 35px; line-height: 38.5px; letter-spacing: -0.2px;
  }
  .flyer__cta {
    display: flex; align-items: center; justify-content: center;
    gap: 4px; margin-top: 10px;
    font-size: 25px; line-height: 26px;
  }
  .flyer__cta::before, .flyer__cta::after {
    content: ""; width: 126px; height: 4px; background: var(--ink);
  }
  .flyer__phone {
    font-size: 52px; line-height: 54px; margin-top: 4px; letter-spacing: 0.3px;
  }
</style>
</head>
<body>
<main class="canvas">
  <article class="flyer flyer--hanging">
    <div class="flyer__photo" role="img" aria-label="Photo: a white and black kitten hanging from a clothesline held by wooden pegs, on a black background"></div>
    <svg class="flyer__curve" viewBox="0 0 518 730" aria-hidden="true">
      <path d="M0 480 Q259 330 518 480 L518 730 L0 730 Z" fill="var(--grey-band)"/>
      <path d="M0 501 Q259 335 518 501 L518 730 L0 730 Z" fill="var(--green)"/>
      <path d="M0 524 Q259 344 518 524 L518 730 L0 730 Z" fill="var(--panel)"/>
    </svg>
    <div class="flyer__copy">
      <p class="flyer__headline">HR issues and complex employment<br>regulations have you hanging?<br>Hold on and</p>
      <p class="flyer__cta">Call a PEO</p>
      <p class="flyer__phone">0100 5550 123 456</p>
    </div>
  </article>

  <article class="flyer flyer--monkey">
    <div class="flyer__photo" role="img" aria-label="Photo: a thoughtful chimpanzee in profile resting its chin on its hand, against a grey studio backdrop"></div>
    <svg class="flyer__curve" viewBox="0 0 518 730" aria-hidden="true">
      <path d="M0 480 Q259 330 518 480 L518 730 L0 730 Z" fill="var(--grey-band)"/>
      <path d="M0 501 Q259 335 518 501 L518 730 L0 730 Z" fill="var(--green)"/>
      <path d="M0 524 Q259 344 518 524 L518 730 L0 730 Z" fill="var(--panel)"/>
    </svg>
    <div class="flyer__copy">
      <p class="flyer__headline">The federal government does<br>not monkey around when it<br>comes to enforcing regulations</p>
      <p class="flyer__cta">Call a PEO</p>
      <p class="flyer__phone">0100 5550 123 456</p>
    </div>
  </article>
</main>
</body>
</html>
```